Brivane Management

We need a web design for a new consulting company, with clients all over the world. The company provides management consulting to the travel industry.

Logo files are attached.

Website must look very corporate and be responsive in design.

Management Consulting

```html
<!DOCTYPE html>
<html lang="en">
<head>
<meta charset="utf-8">
<title>Brivane Management</title>
<link rel="stylesheet" href="https://fonts.googleapis.com/css2?family=Bitter:wght@400;500&family=Roboto:ital,wght@0,400;0,500;0,700;1,400&family=Open+Sans:wght@400;600&display=swap">
<style>
:root{
  --navy:#121a3c;
  --blue:#1b7dcc;
  --blue-dark:#0f5fa6;
  --green:#6cb52d;
  --green-dark:#4f9a18;
  --ink:#222;
  --body:#444;
  --muted:#888;
  --page:#e7e7e7;
  --panel:#f4f4f4;
  --line:#d6d6d6;
  --foot:#1d1d1d;
  --foot-deep:#111;
  --foot-text:#cfcfcf;
}
*{box-sizing:border-box;margin:0;padding:0}
html,body{width:800px;height:1200px;overflow:hidden}
body{position:relative;background:var(--page);font-family:"Roboto",Arial,sans-serif;color:var(--body)}
.abs{position:absolute}
.topline{left:0;top:0;width:800px;height:5px;background:var(--navy)}
.header{left:0;top:5px;width:800px;height:65px;background:linear-gradient(#fff,#eef0f2)}
.brand{left:92px;top:20px;display:flex;align-items:center;gap:10px;font-family:"Bitter",Georgia,serif;font-size:25px;font-weight:500;color:var(--navy)}
.brand-dot{width:28px;height:28px;border-radius:50%;background:var(--blue)}
.helpline{left:603px;top:25px;display:flex;gap:8px;align-items:center}
.helpline-icon{width:25px;height:25px;border-radius:4px;background:#333;display:flex;align-items:center;justify-content:center}
.helpline small{display:block;font-size:8px;color:#777;letter-spacing:.5px;font-family:"Open Sans",Arial,sans-serif}
.helpline strong{display:block;font-size:13px;color:#333;font-weight:700}
.nav{left:0;top:70px;width:800px;height:29px;background:linear-gradient(#2c95e0,var(--blue-dark))}
.nav ul{list-style:none;display:flex;position:absolute;left:89px;top:0;height:29px}
.nav li{font-family:"Bitter",Georgia,serif;font-size:12px;color:#fff;letter-spacing:.6px;line-height:29px;padding:0 17px;border-right:1px solid rgba(255,255,255,.25)}
.nav li.active{background:linear-gradient(#86c94a,var(--green-dark));width:68px;padding:0;text-align:center}
.search{left:577px;top:73px;width:134px;height:23px;background:#fff;border-radius:2px}
.search span{position:absolute;left:8px;top:6px;font-size:7px;color:#aaa}
.search-btn{position:absolute;right:0;top:0;width:25px;height:23px;background:#222;border-radius:0 2px 2px 0;display:flex;align-items:center;justify-content:center}
.hero{left:0;top:99px;width:800px;height:255px;background:linear-gradient(100deg,#3d4653 0%,#c9ccd0 22%,#e9ebed 45%,#b7bcc3 62%,#e4e5e7 78%,#2e323a 100%)}
.hero-arrow{top:106px;width:22px;height:22px;border-radius:50%;background:rgba(0,0,0,.35);display:flex;align-items:center;justify-content:center}
.hero-caption{left:0;top:224px;width:800px;height:31px;background:rgba(20,20,20,.6);color:#fff;text-align:center;font-family:"Bitter",Georgia,serif;font-size:18px;line-height:31px;letter-spacing:.3px}
.main{left:89px;top:354px;width:625px;height:601px;background:#fff;box-shadow:0 0 6px rgba(0,0,0,.15)}
.card{top:373px;width:188px;height:176px;border:1px solid var(--line);border-radius:6px;background:#fff;overflow:hidden;box-shadow:0 4px 6px -3px rgba(0,0,0,.15)}
.card-head{height:33px;background:linear-gradient(#fff,#eee);border-bottom:1px solid var(--line);display:flex;align-items:center;padding-left:8px;gap:6px;font-size:13px;font-weight:500;color:var(--ink);text-transform:uppercase}
.card-head em{font-style:normal;color:var(--green)}
.mark{width:22px;height:22px;border-radius:50%;border:3px solid var(--blue)}
.card-body{padding:7px 8px;font-size:8.6px;line-height:12px;color:#444}
.card-plus{position:absolute;right:0;bottom:0;width:28px;height:28px;background:linear-gradient(135deg,transparent 50%,var(--blue) 50%)}
.card-plus::after{content:"+";position:absolute;right:4px;bottom:-1px;color:#fff;font-weight:700;font-size:14px}
.news{display:flex;gap:8px;padding:0 0 7px;margin-bottom:8px;border-bottom:1px solid #e2e2e2}
.date{width:21px;flex:none;text-align:center;font-size:7px;font-weight:700;color:#fff;line-height:10px}
.date b{display:block;background:#888}
.date i{display:block;font-style:normal;background:#555}
.news h4{font-size:8.6px;color:#222;font-weight:700;margin-bottom:3px}
.news p{font-size:8.6px;line-height:11.5px}
.field{margin:0 6px 6px;border:1px solid #ccc;border-radius:2px;height:22px;font-size:8.5px;color:#666;padding:5px 6px}
.field.tall{height:52px}
.services-band{left:89px;top:584px;width:625px;height:264px;background:linear-gradient(#f7f7f7,#fff)}
.services-tab{left:326px;top:584px;width:140px;height:20px;background:linear-gradient(#fdfdfd,#ddd);clip-path:polygon(0 0,100% 0,90% 100%,10% 100%);text-align:center;font-size:12px;font-weight:700;color:#333;line-height:19px}
.services-tab em{font-style:normal;color:var(--green)}
.service{width:290px;height:64px;border-top:1px solid #ddd}
.service-icon{position:absolute;left:11px;top:0;width:56px;height:48px;border-radius:0 0 4px 4px;background:linear-gradient(#fafafa,#dcdcdc);border:1px solid #ccc;border-top:2px solid var(--green);display:flex;align-items:center;justify-content:center}
.service h3{position:absolute;left:78px;top:4px;font-size:11.5px;font-weight:700;color:#222}
.service p{position:absolute;left:78px;top:20px;width:212px;font-size:8.6px;line-height:12px;color:#444}
.testimonial{left:89px;top:848px;width:625px;height:107px;background:#e9e9e9}
.avatar{left:106px;top:868px;width:57px;height:57px;border-radius:50%;background:linear-gradient(#dfe6ee,#8a96a8);border:3px solid #fff;box-shadow:0 0 2px #aaa}
.quote{left:190px;top:871px;width:500px;font-size:9px;line-height:14.5px;font-style:italic;color:#333}
.quote-rule{left:190px;top:919px;width:497px;height:1px;background:#bbb}
.quote-name{left:192px;top:927px;font-size:9px;font-weight:700;color:var(--blue-dark)}
.dots{left:648px;top:934px;display:flex;gap:4px}
.dots span{width:6px;height:6px;border-radius:50%;background:#ccc}
.dots span:first-child{background:var(--green)}
.footer{left:0;top:955px;width:800px;height:215px;background:linear-gradient(#2a2a2a,var(--foot) 30%,#161616)}
.newsletter{left:95px;top:967px;width:611px;height:40px;background:var(--foot-deep);border-radius:2px}
.newsletter h2{position:absolute;left:13px;top:8px;font-family:"Open Sans",Arial,sans-serif;font-weight:400;font-size:17px;color:#eee}
.newsletter p{position:absolute;left:165px;top:8px;width:150px;padding-left:12px;border-left:1px solid #333;font-family:"Open Sans",Arial,sans-serif;font-size:9px;line-height:13px;color:#ccc}
.newsletter .email{position:absolute;left:332px;top:11px;width:188px;height:19px;background:#fff;border-radius:2px;font-size:8px;color:#777;padding:5px 6px}
.newsletter .subscribe{position:absolute;left:524px;top:11px;width:76px;height:19px;background:var(--green);border-radius:2px;color:#fff;font-size:10px;font-weight:700;text-align:center;line-height:19px}
.foot-title{top:1041px;font-family:"Open Sans",Arial,sans-serif;font-size:12px;font-weight:600;color:#f2f2f2}
.links{font-family:"Open Sans",Arial,sans-serif;font-size:9px;color:var(--foot-text)}
.links li{list-style:none;height:29px;padding-left:12px;border-bottom:1px solid #2d2d2d;width:80px;line-height:16px;position:relative}
.links li::before{content:"›";position:absolute;left:2px;color:#666}
.contact-row{left:320px;display:flex;gap:10px;font-family:"Open Sans",Arial,sans-serif;font-size:9px;line-height:12px;color:var(--foot-text)}
.contact-row svg{flex:none;margin-top:1px}
.foot-brand{left:543px;top:1060px;display:flex;flex-direction:column;align-items:center;gap:8px;width:156px;font-family:"Bitter",Georgia,serif;font-size:20px;color:#eee}
.foot-brand span{width:40px;height:40px;border-radius:50%;background:#eee}
.bottom{left:0;top:1170px;width:800px;height:30px;background:var(--foot-deep)}
.copyright{left:102px;top:1180px;font-family:"Open Sans",Arial,sans-serif;font-size:8px;color:#bbb}
.copyright b{color:#eee}
.follow{left:555px;top:1174px;display:flex;align-items:center;gap:5px;font-family:"Open Sans",Arial,sans-serif;font-size:10px;color:#eee;letter-spacing:.5px}
.follow span{width:19px;height:19px;border-radius:50%;background:#eee}
.follow span.on{background:var(--green)}
</style>
</head>
<body>
<div class="abs topline"></div>
<header class="abs header"></header>
<div class="abs brand"><span class="brand-dot"></span>Brivane Management</div>
<div class="abs helpline">
  <div class="helpline-icon"><svg width="12" height="12" viewBox="0 0 24 24"><path fill="#fff" d="M6.6 10.8a15 15 0 0 0 6.6 6.6l2.2-2.2c.3-.3.7-.4 1-.2 1.1.4 2.3.6 3.6.6.6 0 1 .4 1 1V20c0 .6-.4 1-1 1A17 17 0 0 1 3 4c0-.6.4-1 1-1h3.5c.6 0 1 .4 1 1 0 1.3.2 2.5.6 3.6.1.3 0 .7-.2 1z"/></svg></div>
  <div><small>HAPPY TO HELP?</small><strong>010-555-0147</strong></div>
</div>

<nav class="abs nav"><ul><li class="active">HOME</li><li>ABOUT</li><li>SERVICES</li><li>RESOURCES</li><li>CONTACT</li></ul></nav>
<div class="abs search"><span>search...</span><div class="search-btn"><svg width="11" height="11" viewBox="0 0 12 12"><circle cx="5" cy="5" r="3.5" stroke="#fff" stroke-width="1.6" fill="none"/><path d="M7.6 7.6 11 11" stroke="#fff" stroke-width="1.8"/></svg></div></div>

<section class="abs hero" role="img" aria-label="Photo of business people in suits shaking hands and applauding in a bright office">
  <div class="abs hero-arrow" style="left:56px"><svg width="8" height="10"><path d="M6 1 2 5l4 4" stroke="#fff" fill="none" stroke-width="1.5"/></svg></div>
  <div class="abs hero-arrow" style="left:724px"><svg width="8" height="10"><path d="M2 1l4 4-4 4" stroke="#fff" fill="none" stroke-width="1.5"/></svg></div>
  <div class="abs hero-caption">We Provides Management Consulting to the Travel Industry</div>
</section>

<main class="abs main"></main>

<article class="abs card" style="left:100px">
  <div class="card-head"><span class="mark"></span>About&nbsp;<em>Brivane</em></div>
  <div class="card-body">Lorem diam nonummy nibh esmod tincidu uta oreet dolore magna quam eratlutpat.nim ad minim veniam, quis nostrud nim adminim veniam, quis nostrud tationau ulamcorper scipit lortis nisl utnim ad minima veniarwem, quis nostrud exercitu ulamco suscipit lobortis nisl utnim nim veniam, quis nostrud exerci scipit lortis nisl utnim ad minima veniarwem, nisl utnim nim veniam, quis nostrud exerci tation ulamcorper suscipit</div>
  <div class="card-plus"></div>
</article>

<article class="abs card" style="left:307px">
  <div class="card-head"><span class="mark"></span>Latest&nbsp;<em>News</em></div>
  <div class="card-body">
    <div class="news"><div class="date"><b>09</b><i>OCT</i></div><div><h4>Lorem ipsum dolor sit amet</h4><p>is nisl utnim ad minima venam, quis nostrud exercin ulamcocipit lobortis nisl utnim nim veniam,is nisl utnimi ad minima veniam, quis</p></div></div>
    <div class="news" style="border:0"><div class="date"><b>09</b><i>OCT</i></div><div><h4>Lorem ipsum dolor sit amet</h4><p>Lorem ipsum smet consectetur mini adipisic elitsed do eit eim adosi miie vnioremipsuma</p></div></div>
  </div>
  <div class="card-plus"></div>
</article>

<article class="abs card" style="left:514px">
  <div class="card-head"><span class="mark"></span>Quick&nbsp;<em>Contact</em></div>
  <div style="padding-top:10px">
    <div class="field">Name</div><div class="field">Email</div><div class="field tall">Message</div>
  </div>
  <div class="card-plus"></div>
</article>

<div class="abs services-band"></div>
<div class="abs services-tab">OUR <em>SERVICES</em></div>

<div class="abs service" style="left:100px;top:622px">
  <div class="service-icon"><svg width="32" height="28" viewBox="0 0 32 28"><rect x="3" y="18" width="4" height="8" fill="#222"/><rect x="9" y="14" width="4" height="12" fill="#222"/><rect x="15" y="11" width="4" height="15" fill="#222"/><rect x="21" y="8" width="4" height="18" fill="#222"/><path d="M3 14 22 3" stroke="var(--blue)" stroke-width="2.5"/><path d="M18 2h6v6z" fill="var(--blue)"/></svg></div>
  <h3>Sales/ Marketing</h3><p>Lorem ipsum dolor sit amet consectetur elitsed do eiusmod tempor incididunt ut labore et dolore magna aliqua ut enim ad minim vesniam.</p>
</div>
<div class="abs service" style="left:417px;top:622px">
  <div class="service-icon"><svg width="32" height="28" viewBox="0 0 32 28"><circle cx="12" cy="7" r="5" fill="#222"/><path d="M2 26c0-8 4-12 10-12s10 4 10 12z" fill="#222"/><circle cx="23" cy="20" r="7" fill="var(--blue)"/><path d="M23 16v4h3" stroke="#fff" stroke-width="1.5" fill="none"/></svg></div>
  <h3>Strategic Planning</h3><p>Lorem ipsum dolor sit amet consectetur elitsed do eiusmod tempor incididunt ut labore et dolore magna aliqua ut enim ad minim vesniam.</p>
</div>
<div class="abs service" style="left:100px;top:695px">
  <div class="service-icon"><svg width="32" height="30" viewBox="0 0 32 30"><circle cx="11" cy="4" r="3.5" fill="#222"/><rect x="7" y="9" width="8" height="12" rx="2" fill="#222"/><rect x="7" y="20" width="3" height="9" fill="#222"/><rect x="12" y="20" width="3" height="9" fill="#222"/><circle cx="21" cy="18" r="7" fill="#fff" stroke="var(--blue)" stroke-width="2"/><text x="21" y="22" font-size="10" font-weight="700" text-anchor="middle" fill="var(--blue)" font-family="Roboto,sans-serif">$</text></svg></div>
  <h3>Human Capital Management Solutions</h3><p>Lorem ipsum dolor sit amet consectetsed do eiusmod tempor incididunt ut labore et dolore magna aliqua ut enim ad minim vesniam.</p>
</div>
<div class="abs service" style="left:417px;top:695px">
  <div class="service-icon"><svg width="34" height="28" viewBox="0 0 34 28"><rect x="2" y="3" width="24" height="17" fill="#fff" stroke="#222" stroke-width="2.5"/><path d="M5 16l5-6 4 4 5-7 4 4" stroke="#222" stroke-width="2" fill="none"/><circle cx="24" cy="18" r="5" fill="#fff" stroke="var(--blue)" stroke-width="2.5"/><path d="M27.5 21.5 32 26" stroke="var(--blue)" stroke-width="3"/></svg></div>
  <h3>Financial Analysis</h3><p>Lorem ipsum dolor sit amet consectetur elitsed do eiusmod tempor incididunt ut labore et dolore magna aliqua ut enim ad minim vesniam.</p>
</div>
<div class="abs service" style="left:100px;top:773px">
  <div class="service-icon"><svg width="36" height="28" viewBox="0 0 36 28"><rect x="11" y="2" width="10" height="5" rx="1" fill="none" stroke="#222" stroke-width="2"/><rect x="2" y="6" width="28" height="19" rx="2" fill="#222"/><rect x="2" y="13" width="28" height="2" fill="#888"/><circle cx="29" cy="21" r="6" fill="var(--blue)"/><text x="29" y="25" font-size="9" font-weight="700" text-anchor="middle" fill="#fff" font-family="Roboto,sans-serif">$</text></svg></div>
  <h3>Cash Management Solutions</h3><p>Lorem ipsum dolor sit amet consectetur elitsed do eiusmod tempor incididunt ut labore et dolore magna aliqua ut enim ad minim vesniam.</p>
</div>
<div class="abs service" style="left:417px;top:773px">
  <div class="service-icon"><svg width="32" height="30" viewBox="0 0 32 30"><path d="M6 16a10 10 0 0 1 20 0" stroke="#222" stroke-width="3" fill="none"/><rect x="3" y="14" width="6" height="10" rx="2" fill="#222"/><rect x="23" y="14" width="6" height="10" rx="2" fill="#222"/><path d="M26 24c0 3-4 4-8 4" stroke="var(--blue)" stroke-width="2" fill="none"/><circle cx="17" cy="28" r="2" fill="var(--blue)"/></svg></div>
  <h3>Customer Support</h3><p>Lorem ipsum dolor sit amet consectetur elitsed do eiusmod tempor incididunt ut labore et dolore magna aliqua ut enim ad minim vesniam.</p>
</div>

<section class="abs testimonial"></section>
<div class="abs avatar" role="img" aria-label="Portrait photo of the client giving the testimonial"></div>
<svg class="abs" style="left:178px;top:865px" width="14" height="12"><text x="0" y="14" font-size="22" fill="#bbb" font-family="Georgia,serif">“</text></svg>
<p class="abs quote">Lorem ipsum dolor sit amet consectetur adipisicing elitsed do eiusmod tempor incididunt ut labore et dolore magna aliqua. Ut enim ad minim vesniam, quis nostrud exercitation ullamco laboris nisi ut aliquip ex ea commodo consequat. Duis aute irure dolor in reprehenderit in voluptate velit esse cillum is a dolore eu fugiat nulla pariatur. Excepteur sint occaecat cupidatat non proi</p>
<svg class="abs" style="left:650px;top:897px" width="16" height="16"><text x="0" y="22" font-size="22" fill="#bbb" font-family="Georgia,serif">”</text></svg>
<div class="abs quote-rule"></div>
<div class="abs quote-name">Daniel Harper</div>
<div class="abs dots"><span></span><span></span><span></span><span></span></div>

<footer class="abs footer"></footer>
<div class="abs newsletter">
  <h2>Newsletter Signup</h2>
  <p>Get latest updates by entering your email address.</p>
  <div class="email">Enter your Email...</div>
  <div class="subscribe">SUBSCRIBE</div>
</div>

<h3 class="abs foot-title" style="left:102px">QUICK LINKS</h3>
<ul class="abs links" style="left:103px;top:1071px"><li>Home</li><li>Services</li><li>Contact Us</li></ul>
<ul class="abs links" style="left:203px;top:1074px"><li>About Us</li><li>Resources</li></ul>

<h3 class="abs foot-title" style="left:320px">CONTACT US</h3>
<div class="abs contact-row" style="top:1074px"><svg width="9" height="11" viewBox="0 0 10 13"><path d="M5 0a5 5 0 0 1 5 5c0 3-5 8-5 8S0 8 0 5a5 5 0 0 1 5-5z" fill="#eee"/><circle cx="5" cy="5" r="2" fill="#1d1d1d"/></svg><span>Lorem ipsum dolor sit amet consecttuer adi<br>piscing elit diam non</span></div>
<div class="abs contact-row" style="top:1106px"><svg width="9" height="9" viewBox="0 0 24 24"><path fill="#eee" d="M6.6 10.8a15 15 0 0 0 6.6 6.6l2.2-2.2c.3-.3.7-.4 1-.2 1.1.4 2.3.6 3.6.6.6 0 1 .4 1 1V20c0 .6-.4 1-1 1A17 17 0 0 1 3 4c0-.6.4-1 1-1h3.5c.6 0 1 .4 1 1 0 1.3.2 2.5.6 3.6.1.3 0 .7-.2 1z"/></svg><span>010-555-0147</span></div>
<div class="abs contact-row" style="top:1127px"><svg width="10" height="8" viewBox="0 0 10 8"><rect width="10" height="8" fill="#eee"/><path d="M0 0l5 4 5-4" stroke="#1d1d1d" fill="none"/></svg><span>info@brivanemgmt.com</span></div>

<div class="abs foot-brand"><span></span>Brivane Management</div>

<div class="abs bottom"></div>
<p class="abs copyright">Copyright 2014 <b>brivanemanagement.</b> All Right Reserved.</p>
<div class="abs follow">FOLLOW US :&nbsp;<span class="on"></span><span></span><span></span><span></span></div>
</body>
</html>
```